Need a new company business card

I am looking for a new company business card. Front and back. With information on it as per below. Card should be professional. Yet clever. Simple. Modern design. Pim card, traditional size. OK with say, all black or all red backside.

Varnholt is an indie, bootstrapped magazine advancing the work of intersectional feminists busting their buts to create a just world through the power of enterprise and innovation.

Varnholt is the home and voice of entrepreneurial feminism and feminist innovators worldwide. Entrepreneurial feminists are people (of all genders) who see inequality as an innovation priority. They work to advance gender equity and/or who strive to integrate and practice feminist principles, pedagogy, values into their innovation and entrepreneurship work.
We are committed to this space being trans and queer inclusive, anti-racist, intersectional, brave, and safe. We welcome all allies. We value learning, edgy but civil discourse and integrative thinking skills.

Target Market(s)

feminists, business owners,

Industry/Entity Type

Publishing Company

Contact Information for Business Card

RD Tolliver
Founder/Publisher
4-237 Ashgrove Lane, Toronto, ON
M4T 2K8
publisher@varnholt.com
416-552-3019
www.varnholt.com

Font styles to use
Serif
Other font styles liked:
• Myriad Pro

Colors
ec1f27
000000
ffffff

Requirements
Must have
• logo
• use red, black white colours only.
Nice to have
• use the compass in pattern or creatively but not too busy please
Should not have
• Should not be too busy. Elegant.

```html
<!DOCTYPE html>
<html lang="en">
<head>
<meta charset="utf-8">
<title>Varnholt business card</title>
<link rel="stylesheet" href="https://fonts.googleapis.com/css2?family=Source+Sans+3:wght@400;700&family=Roboto:wght@400;500;700&display=swap">
<style>
  :root {
    --red: #ec1f27;
    --ink: #2f3031;
    --white: #ffffff;
    --paper: #f4f4f2;
    --stage: #e7e4df;
  }
  * { box-sizing: border-box; margin: 0; padding: 0; }
  html, body { width: 1200px; height: 886px; overflow: hidden; }
  body {
    background: var(--stage);
    display: flex;
    align-items: center;
    justify-content: center;
    gap: 40px;
  }
  .card {
    width: 540px;
    height: 309px;
    position: relative;
    overflow: hidden;
    background: var(--red);
    color: var(--white);
    box-shadow: 0 6px 18px rgba(0,0,0,0.18);
  }

  .brand {
    position: absolute;
    left: 0; right: 0;
    display: flex;
    flex-direction: column;
    align-items: center;
  }
  .brand-row { display: flex; align-items: flex-start; gap: 6px; }
  .brand-name {
    font-family: "Source Sans 3", sans-serif;
    font-weight: 700;
    font-size: 72px;
    line-height: 0.95;
    letter-spacing: -1px;
  }
  .brand-dot {
    width: 15px; height: 15px;
    margin-top: 2px;
    border: 1.6px solid currentColor;
    border-radius: 50%;
  }
  .brand-line {
    font-family: "Source Sans 3", sans-serif;
    font-weight: 400;
    font-size: 11px;
    letter-spacing: 1.6px;
    text-transform: uppercase;
    margin-top: 8px;
    margin-right: 21px;
  }

  .card-front .brand { top: 88px; }
  .front-url {
    position: absolute;
    left: 0; right: 0; bottom: 46px;
    text-align: center;
    font-family: "Source Sans 3", sans-serif;
    font-size: 13px;
    letter-spacing: 7px;
  }

  .back-top {
    position: absolute;
    left: 0; top: 0;
    width: 100%; height: 176px;
    background: var(--paper);
    color: var(--ink);
  }
  .card-back .brand { top: 46px; }

  .contact {
    position: absolute;
    right: 26px; top: 190px;
    list-style: none;
    font-family: "Roboto", sans-serif;
    font-size: 13px;
    line-height: 18px;
  }
  .contact li { display: flex; justify-content: flex-end; align-items: center; gap: 7px; }
  .contact svg { width: 11px; height: 11px; fill: var(--white); flex: none; }

  .person {
    position: absolute;
    left: 26px; bottom: 22px;
    font-family: "Roboto", sans-serif;
  }
  .person-name { font-size: 18px; font-weight: 700; line-height: 21px; }
  .person-role { font-size: 15px; font-weight: 500; line-height: 19px; }
  .person-address { font-size: 13.5px; line-height: 17px; margin-top: 3px; font-style: normal; }
</style>
</head>
<body>
  <section class="card card-front">
    <div class="brand">
      <div class="brand-row">
        <span class="brand-name">Varnholt</span>
        <span class="brand-dot"></span>
      </div>
      <span class="brand-line">A magazine for entrepreneurial feminists</span>
    </div>
    <p class="front-url">www.varnholt.com</p>
  </section>

  <section class="card card-back">
    <div class="back-top">
      <div class="brand">
        <div class="brand-row">
          <span class="brand-name">Varnholt</span>
          <span class="brand-dot"></span>
        </div>
        <span class="brand-line">A magazine for entrepreneurial feminists</span>
      </div>
    </div>

    <ul class="contact">
      <li>416-552-3019
        <svg viewBox="0 0 24 24"><path d="M6.6 10.8a15.1 15.1 0 0 0 6.6 6.6l2.2-2.2a1 1 0 0 1 1-.25 11.4 11.4 0 0 0 3.6.57 1 1 0 0 1 1 1V20a1 1 0 0 1-1 1A17 17 0 0 1 3 4a1 1 0 0 1 1-1h3.5a1 1 0 0 1 1 1c0 1.25.2 2.45.57 3.57a1 1 0 0 1-.25 1z"/></svg>
      </li>
      <li>publisher@varnholt.com
        <svg viewBox="0 0 24 24"><path d="M2 5h20v2l-10 7L2 7z M2 9l10 7 10-7v10H2z"/></svg>
      </li>
      <li>www.varnholt.com
        <svg viewBox="0 0 24 24"><circle cx="12" cy="12" r="10"/><path d="M2 12h20M12 2c3 3 3 17 0 20M12 2c-3 3-3 17 0 20" fill="none" stroke="#ec1f27" stroke-width="1.6"/></svg>
      </li>
    </ul>

    <div class="person">
      <p class="person-name">RD TOLLIVER</p>
      <p class="person-role">Founder/Publisher</p>
      <address class="person-address">4-237 Ashgrove Lane<br>Toronto, ON, M4T 2K8</address>
    </div>
  </section>
</body>
</html>
```